Website design for legal tech start up in Switzerland (B2B)

We are for a legal tech start up in Switzerland called KOVA. We have been running since August 2016. This will be our first live website.

We need a website designed and business card design for our start-up in Switzerland. We also need the Web design to be converted into HTML and CSS files.

Function of website:
• To inform potential customers of our services
• Form a key part of our digital marketing and sales footprint.
• Branding

Please find attached logo.
Updates

Project Deadline Extended Reason: Giving us time to review submissions and provide opportunity for more submissions. Added Thursday, February 16, 2017

Project Deadline Extended
Reason: Looking for more idea's not necessarily set on blue and grey colours only.

Target Market(s)

B2B tech powered legal services.

Industry/Entity Type

Legal

Contact Information for Business Card

Lean and slick design.

Coding

Coded - Design and coding required

Number of Pages Required

5+ page

Requirements
Must have
• VERY LEAN AND CLEAN DESIGN!
• We have received many great standard designs, but we are looking for something more out-of-the box: You can get inspiration from these designs: http://www.pixelvane.com/websites/clean/
• Thanks!!
• Easy content management system
• Well structured coding for additional development
• Responsive webpage for all types of devices
• SEO optimized
• Tabs (Home, services, team, careers, blog, contact us)
• Colour scheme complementary to logo
Nice to have
• Look and Design - Approachable, High-tech, Modern
• Easy to add chat bot capability in future
Should not have
• Too busy/ too much clutter
• Not take to long to load

```html
<!DOCTYPE html>
<html lang="en">
<head>
<meta charset="utf-8">
<title>KOVA — Legal Tech</title>
<link href="https://fonts.googleapis.com/css2?family=Lato:wght@300;400;700;900&display=swap" rel="stylesheet">
<style>
:root{
  --navy:#1c3766;
  --navy-dark:#142a50;
  --ink:#2d2d2d;
  --grey:#4a4a4a;
  --muted:#777;
  --light:#f1f1f1;
  --line:#cfcfcf;
  --white:#fff;
  --footer:#14161c;
}
*{box-sizing:border-box;margin:0;padding:0}
html,body{width:1200px;height:3448px;overflow:hidden}
body{font-family:"Lato",Arial,sans-serif;color:var(--ink);background:var(--white);position:relative}
.abs{position:absolute}

/* header */
.site-header{position:absolute;left:0;top:0;width:1200px;height:115px;background:var(--white)}
.brand{position:absolute;left:80px;top:14px;font-weight:900;font-size:84px;letter-spacing:2px;color:#3a3a3a;line-height:1}
.header-phone{position:absolute;right:80px;top:24px;display:flex;align-items:center;gap:10px;font-size:22px;color:var(--navy);font-weight:700}
.round-icon{width:34px;height:34px;border-radius:50%;background:var(--navy);display:flex;align-items:center;justify-content:center}
.main-nav{position:absolute;right:78px;top:76px;display:flex;gap:36px;font-size:16px;font-weight:700;color:var(--ink)}
.main-nav a{color:inherit;text-decoration:none;padding-bottom:8px}
.main-nav a.active{color:var(--navy);border-bottom:3px solid var(--navy)}
.nav-mark{position:absolute;left:590px;top:44px;color:#bbb;font-size:22px;font-weight:300}

/* hero */
.hero{position:absolute;left:0;top:115px;width:1200px;height:533px;overflow:hidden}
.hero-photo{position:absolute;inset:0;background:linear-gradient(100deg,#9aa1ab 0%,#c9ced6 45%,#e4e6ea 70%,#8d96a3 100%)}
.hero-shape{position:absolute;left:0;top:0}
.hero-title{position:absolute;left:83px;top:205px;font-size:40px;font-weight:400;color:var(--white);line-height:58px;letter-spacing:1px}
.btn-outline{position:absolute;left:80px;top:336px;width:315px;height:66px;border:2px solid var(--white);color:var(--white);font-size:19px;font-weight:700;display:flex;align-items:center;justify-content:center;letter-spacing:.5px}

/* about */
.about{position:absolute;left:0;top:648px;width:1200px;height:410px;background:var(--light)}
.about-title{position:absolute;left:80px;top:60px;font-size:38px;font-weight:700}
.about-title span{font-weight:900}
.about-rule{position:absolute;left:80px;top:116px;width:255px;height:2px;background:var(--ink)}
.about-text{position:absolute;left:80px;top:140px;width:655px;font-size:12.5px;line-height:24px;color:var(--grey)}
.feature{position:absolute;top:278px;display:flex;gap:16px;width:300px}
.feature-icon{flex:none;width:82px;height:82px;border-radius:50%;border:3px solid var(--navy);background:var(--white);display:flex;align-items:center;justify-content:center}
.feature h4{font-size:19px;font-weight:400;color:var(--ink);margin-top:4px;margin-bottom:4px}
.feature p{font-size:11.5px;line-height:16px;color:var(--muted)}
.quick-form{position:absolute;left:747px;top:68px;width:357px;height:300px;background:var(--white);box-shadow:0 2px 10px rgba(0,0,0,.1)}
.quick-tab{position:absolute;left:45px;top:-10px;width:290px;height:42px;background:var(--navy);color:var(--white);text-align:center;border-radius:3px}
.quick-tab b{display:block;font-size:16px;font-weight:400;letter-spacing:.5px;padding-top:4px}
.quick-tab small{display:block;font-size:10.5px}
.field{position:absolute;left:25px;width:310px;height:36px;border:1px solid var(--line);background:#f6f6f6;font-size:12px;color:var(--muted);padding:10px 10px;display:flex;justify-content:space-between}
.field i{color:#c0392b;font-style:normal}
.submit{position:absolute;left:25px;top:240px;width:111px;height:35px;background:var(--navy);color:var(--white);font-size:15px;font-weight:700;display:flex;align-items:center;justify-content:center;gap:8px;letter-spacing:1px}

/* section titles */
.sec-title{position:absolute;left:0;width:1200px;text-align:center;font-size:38px;font-weight:700;color:var(--ink)}
.sec-title em{font-style:normal;color:var(--navy)}
.divider{position:absolute;left:330px;width:540px;height:20px}

/* services */
.service-card{position:absolute;width:329px;height:237px;background:var(--white);box-shadow:0 1px 6px rgba(0,0,0,.15)}
.service-media{position:absolute;left:0;top:0;width:329px;height:179px}
.service-badge{position:absolute;left:140px;top:152px;width:50px;height:50px;border-radius:50%;background:var(--white);display:flex;align-items:center;justify-content:center}
.service-badge span{width:36px;height:36px;border-radius:50%;background:#3b3b3b}
.service-name{position:absolute;left:0;top:204px;width:100%;text-align:center;font-size:17px;color:var(--grey)}
.service-card::after{content:"";position:absolute;left:0;bottom:0;width:100%;height:3px;background:#3b3b3b}

/* advice band */
.advice{position:absolute;left:0;top:1722px;width:1200px;height:83px;background:var(--navy);color:var(--white)}
.advice-lead{position:absolute;left:78px;top:25px;font-size:27px;font-weight:400;white-space:nowrap;line-height:34px}
.advice-icon{position:absolute;top:20px;width:44px;height:44px;border-radius:50%;background:#e9e9e9;display:flex;align-items:center;justify-content:center}
.advice-offer{position:absolute;left:494px;top:28px;font-size:21px;white-space:nowrap}
.advice-or{position:absolute;left:800px;top:30px;font-size:18px;color:#6f86b0}
.advice-call{position:absolute;left:914px;top:14px}
.advice-call small{display:block;font-size:12px;color:#b5c3dc}
.advice-call b{display:block;font-size:30px;font-weight:400;line-height:32px}

/* why */
.why{position:absolute;left:0;top:1805px;width:1200px;height:586px;background:linear-gradient(180deg,#f7f7f7,#ececec)}
.why-item{position:absolute;width:290px}
.why-item h4{font-size:19px;font-weight:700;color:var(--ink)}
.why-item p{font-size:13px;line-height:20px;color:var(--muted);margin-top:4px}
.why-item.below{text-align:center}
.dot-arrow{position:absolute;width:24px;height:24px;border-radius:50%;background:#2f2f2f;display:flex;align-items:center;justify-content:center}

/* blog */
.blog-card{position:absolute;top:2552px;width:329px;height:349px;background:var(--white);box-shadow:0 1px 6px rgba(0,0,0,.15)}
.blog-media{position:absolute;left:0;top:0;width:329px;height:184px}
.blog-date{position:absolute;left:17px;top:223px;width:36px;height:40px;border:1px solid var(--line);text-align:center;font-size:12px;line-height:18px}
.blog-date b{display:block;background:var(--navy);color:var(--white);font-weight:700}
.blog-date small{font-size:8px;color:var(--muted)}
.blog-body{position:absolute;left:70px;top:220px;width:245px}
.blog-body h5{font-size:14px;font-weight:400;color:var(--ink)}
.blog-body .meta{font-size:11.5px;color:var(--muted);margin-top:7px}
.blog-body p{font-size:12px;line-height:24px;color:var(--muted);margin-top:5px}
.pager{position:absolute;top:2930px;left:584px;display:flex;gap:10px}
.pager span{width:11px;height:11px;border-radius:50%;border:1px solid var(--navy)}
.pager span.on{background:var(--navy)}

/* footer */
.site-footer{position:absolute;left:0;top:2966px;width:1200px;height:482px;background:linear-gradient(180deg,#1d2129 0%,#101319 60%,#0c0e12 100%);color:var(--white)}
.contact-col{position:absolute;top:48px;width:320px;text-align:center;font-size:12.5px}
.contact-col svg{display:block;margin:0 auto 18px}
.contact-col.bordered{border-right:1px solid rgba(255,255,255,.25)}
.footer-brand{position:absolute;left:0;top:145px;width:100%;text-align:center;font-size:56px;font-weight:900;letter-spacing:2px;line-height:1}
.footer-text{position:absolute;left:300px;top:222px;width:600px;text-align:center;font-size:12.5px;line-height:20px;color:#d0d0d0}
.hours{position:absolute;top:290px;left:0;width:100%;display:flex;justify-content:center;gap:12px}
.hours span{background:#2a3a5c;padding:7px 14px;font-size:12px;font-weight:700}
.footer-btn{position:absolute;left:540px;top:344px;width:122px;height:32px;border:1px solid var(--white);font-size:13px;display:flex;align-items:center;justify-content:center;letter-spacing:.5px}
.footer-rule{position:absolute;left:0;top:400px;width:100%;height:1px;background:rgba(255,255,255,.2)}
.copyright{position:absolute;left:82px;top:436px;font-size:13px;color:#d0d0d0}
.social{position:absolute;top:426px;width:38px;height:38px;border-radius:50%;border:2px solid var(--white)}
</style>
</head>
<body>

<header class="site-header">
  <div class="brand">KOVA</div>
  <div class="nav-mark">×</div>
  <div class="header-phone">
    <span class="round-icon"><svg width="18" height="18" viewBox="0 0 24 24"><path fill="#fff" d="M6.6 10.8c1.4 2.8 3.8 5.1 6.6 6.6l2.2-2.2c.3-.3.7-.4 1-.2 1.1.4 2.3.6 3.6.6.6 0 1 .4 1 1V20c0 .6-.4 1-1 1C10.6 21 3 13.4 3 4c0-.6.4-1 1-1h3.5c.6 0 1 .4 1 1 0 1.3.2 2.5.6 3.6.1.3 0 .7-.2 1z"/></svg></span>
    +123 456 7890
  </div>
  <nav class="main-nav">
    <a class="active">HOME</a><a>SERVICES</a><a>TEAM</a><a>CAREERS</a><a>BLOG</a><a>CONTACT US</a>
  </nav>
</header>

<section class="hero">
  <div class="hero-photo" role="img" aria-label="Photo of two business advisors reviewing work together"></div>
  <svg class="hero-shape" width="1200" height="533" viewBox="0 0 1200 533">
    <defs><linearGradient id="heroShade" x1="0" x2="1"><stop offset="0" stop-color="#3c3d40"/><stop offset="1" stop-color="#2a2b2e"/></linearGradient></defs>
    <polygon points="0,0 490,0 680,266 490,533 0,533" fill="url(#heroShade)" opacity=".96"/>
  </svg>
  <h1 class="hero-title">WE ARE EXPERT IN<br>LEGAL ADVISOR</h1>
  <div class="btn-outline">GET A FREE CONSULTATION</div>
</section>

<section class="about">
  <h2 class="about-title">ABOUT <span>KOVA</span></h2>
  <div class="about-rule"></div>
  <p class="about-text">eaque ipsa quae ab illo inventore veritatis et quasi architecto beatae vitae dicta sunt explicaboSed ut perspiciatis unde omnis iste natus error sit voluptatem accusantium dolo remque laudantium, totam rem aperiam, eaque ipsa quae ab illo inventore veritatis et quasi architecto beatae vitae dicta sunt explicabo Sed ut perspiciatis unde omnis iste natus error sit voluptatem accusantium dolo.eaque ipsa quae ab illo inventore veritatis et quasi architecto beatae vitae dicta sunt explicabo.</p>

  <div class="feature" style="left:82px">
    <div class="feature-icon"><svg width="40" height="34" viewBox="0 0 40 34"><circle cx="20" cy="9" r="6" fill="#1c3766"/><circle cx="8" cy="13" r="4.5" fill="#1c3766"/><circle cx="32" cy="13" r="4.5" fill="#1c3766"/><path d="M10 32c0-7 4-13 10-13s10 6 10 13z" fill="#1c3766"/><path d="M0 32c0-5 3-10 8-10 2 0 3 .5 4 1-2 3-3 6-3 9z M40 32c0-5-3-10-8-10-2 0-3 .5-4 1 2 3 3 6 3 9z" fill="#1c3766"/></svg></div>
    <div><h4>Our Misshion</h4><p>Sed ut perspiciatis unde omnis iste natus error sit voluptatem accusantium</p></div>
  </div>
  <div class="feature" style="left:380px">
    <div class="feature-icon"><svg width="40" height="40" viewBox="0 0 40 40"><circle cx="20" cy="20" r="16" fill="none" stroke="#1c3766" stroke-width="3"/><circle cx="20" cy="20" r="9" fill="none" stroke="#1c3766" stroke-width="3"/><circle cx="20" cy="20" r="3" fill="#1c3766"/><path d="M20 20L36 4" stroke="#1c3766" stroke-width="3"/></svg></div>
    <div><h4>Our Vision</h4><p>Sed ut perspiciatis unde omnis iste natus error sit voluptatem accusantium .</p></div>
  </div>

  <form class="quick-form">
    <div class="quick-tab"><b>QUICK CONTACT WITH US</b><small>Get a FREE Consultation</small></div>
    <div class="field" style="top:60px">Name <i>*</i></div>
    <div class="field" style="top:106px">Email <i>*</i></div>
    <div class="field" style="top:152px">Phone <i>*</i></div>
    <div class="field" style="top:198px">Select Services <svg width="12" height="12" viewBox="0 0 12 12"><path d="M2 4l4 4 4-4" stroke="#555" stroke-width="2" fill="none"/></svg></div>
    <div class="submit">SUBMIT <svg width="14" height="12" viewBox="0 0 14 12"><path d="M1 1l5 5-5 5M7 1l5 5-5 5" stroke="#fff" stroke-width="2" fill="none"/></svg></div>
  </form>
</section>

<h2 class="sec-title" style="top:1075px">OUR SERVICES</h2>
<svg class="divider" style="top:1128px" viewBox="0 0 540 20"><line x1="0" y1="10" x2="255" y2="10" stroke="#ccc"/><line x1="285" y1="10" x2="540" y2="10" stroke="#ccc"/><path d="M264 4l12 12M276 4l-12 12" stroke="#aaa" stroke-width="2"/></svg>

<article class="service-card" style="left:80px;top:1177px">
  <div class="service-media" role="img" aria-label="Photo of hands on a tablet showing charts" style="background:linear-gradient(135deg,#dfe6ee,#8fb3d8)"></div>
  <div class="service-badge"><span></span></div><div class="service-name">Information Management</div>
</article>
<article class="service-card" style="left:437px;top:1177px">
  <div class="service-media" role="img" aria-label="Photo of a consultant on a phone call at a desk" style="background:linear-gradient(135deg,#e8ecf1,#8ea6c4)"></div>
  <div class="service-badge"><span></span></div><div class="service-name">Case Support</div>
</article>
<article class="service-card" style="left:791px;top:1177px">
  <div class="service-media" role="img" aria-label="Photo of a hand touching a digital interface" style="background:linear-gradient(135deg,#26364f,#5d7fa6)"></div>
  <div class="service-badge"><span></span></div><div class="service-name">Application Development</div>
</article>
<article class="service-card" style="left:80px;top:1444px">
  <div class="service-media" role="img" aria-label="Photo looking up at a green forest canopy" style="background:linear-gradient(135deg,#4f7a2c,#b7d47a)"></div>
  <div class="service-badge"><span></span></div><div class="service-name">Environmental Litigation</div>
</article>
<article class="service-card" style="left:437px;top:1444px">
  <div class="service-media" role="img" aria-label="Photo of a lawyer writing beside a gavel" style="background:linear-gradient(135deg,#3a2a20,#a58662)"></div>
  <div class="service-badge"><span></span></div><div class="service-name">Legal Word Processing</div>
</article>
<article class="service-card" style="left:791px;top:1444px">
  <div class="service-media" role="img" aria-label="Photo of bearings on a technical drawing" style="background:linear-gradient(135deg,#d9d9d9,#8c8c8c)"></div>
  <div class="service-badge"><span></span></div><div class="service-name">Procurement Support</div>
</article>

<section class="advice">
  <div class="advice-lead">NEED A LEGAL ADVICE&nbsp; ?</div>
  <div class="advice-icon" style="left:432px"><svg width="22" height="22" viewBox="0 0 22 22"><circle cx="11" cy="7" r="5" fill="#1c3766"/><path d="M2 21c0-6 4-9 9-9s9 3 9 9z" fill="#1c3766"/></svg></div>
  <div class="advice-offer">Get A FREE CONSULTATION</div>
  <div class="advice-or">OR</div>
  <div class="advice-icon" style="left:856px"><svg width="20" height="20" viewBox="0 0 24 24"><path fill="#1c3766" d="M6.6 10.8c1.4 2.8 3.8 5.1 6.6 6.6l2.2-2.2c.3-.3.7-.4 1-.2 1.1.4 2.3.6 3.6.6.6 0 1 .4 1 1V20c0 .6-.4 1-1 1C10.6 21 3 13.4 3 4c0-.6.4-1 1-1h3.5c.6 0 1 .4 1 1 0 1.3.2 2.5.6 3.6.1.3 0 .7-.2 1z"/></svg></div>
  <div class="advice-call"><small>Call Us Today</small><b>+123 456 7890</b></div>
</section>

<section class="why">
  <h2 class="sec-title" style="top:34px">WHY <em>CHOOSE US ?</em></h2>
  <svg class="divider" style="top:85px" viewBox="0 0 540 20"><line x1="0" y1="10" x2="255" y2="10" stroke="#ccc"/><line x1="285" y1="10" x2="540" y2="10" stroke="#ccc"/><path d="M264 4l12 12M276 4l-12 12" stroke="#aaa" stroke-width="2"/></svg>

  <div class="why-item" style="left:88px;top:143px"><h4>Strategic Planning</h4><p>Duis autem vel eum iriure dolor in<br>hendrerit in vulputate.</p></div>
  <div class="why-item" style="left:421px;top:143px"><h4>Creative</h4><p>Duis autem vel eum iriure dolor in<br>hendrerit in vulputate.</p></div>
  <div class="why-item" style="left:750px;top:143px"><h4>Consulting Practice</h4><p>Duis autem vel eum iriure dolor in<br>hendrerit in vulputate.</p></div>
  <span class="dot-arrow" style="left:170px;top:222px"><svg width="8" height="10" viewBox="0 0 8 10"><path d="M1 1l5 4-5 4" stroke="#fff" stroke-width="2" fill="none"/></svg></span>
  <span class="dot-arrow" style="left:505px;top:222px"><svg width="8" height="10" viewBox="0 0 8 10"><path d="M1 1l5 4-5 4" stroke="#fff" stroke-width="2" fill="none"/></svg></span>
  <span class="dot-arrow" style="left:838px;top:222px"><svg width="8" height="10" viewBox="0 0 8 10"><path d="M1 1l5 4-5 4" stroke="#fff" stroke-width="2" fill="none"/></svg></span>

  <svg class="abs" style="left:0;top:225px" width="1200" height="240" viewBox="0 0 1200 240">
    <path d="M98 120 A84 84 0 0 0 266 120 L236 120 A54 54 0 0 1 128 120Z" fill="#3d3d3f"/>
    <path d="M433 120 A84 84 0 0 0 601 120 L571 120 A54 54 0 0 1 463 120Z" fill="#3d3d3f"/>
    <path d="M767 120 A84 84 0 0 0 935 120 L905 120 A54 54 0 0 1 797 120Z" fill="#3d3d3f"/>
    <path d="M265 120 A84 84 0 0 1 433 120 L403 120 A54 54 0 0 0 295 120Z" fill="#1c3766"/>
    <path d="M599 120 A84 84 0 0 1 767 120 L737 120 A54 54 0 0 0 629 120Z" fill="#1c3766"/>
    <path d="M932 120 A84 84 0 0 1 1100 120 L1070 120 A54 54 0 0 0 962 120Z" fill="#1c3766"/>
    <g fill="#fff" stroke="#e2e2e2" stroke-width="2">
      <circle cx="182" cy="120" r="50"/><circle cx="349" cy="120" r="50"/><circle cx="517" cy="120" r="50"/>
      <circle cx="683" cy="120" r="50"/><circle cx="851" cy="120" r="50"/><circle cx="1016" cy="120" r="50"/>
    </g>
    <g fill="#2b2b2b">
      <rect x="164" y="102" width="18" height="18"/><rect x="184" y="122" width="18" height="18"/><rect x="164" y="122" width="18" height="18" fill="#1c3766"/>
      <rect x="329" y="102" width="36" height="28" fill="none" stroke="#1c3766" stroke-width="3"/><circle cx="362" cy="130" r="8" fill="none" stroke="#2b2b2b" stroke-width="3"/>
      <circle cx="517" cy="112" r="13"/><rect x="510" y="126" width="14" height="10"/>
      <rect x="666" y="122" width="6" height="16" fill="#1c3766"/><rect x="676" y="114" width="6" height="24" fill="#1c3766"/><rect x="686" y="106" width="6" height="32" fill="#1c3766"/><path d="M664 114l14-10 10 6 14-10" stroke="#2b2b2b" stroke-width="3" fill="none"/>
      <rect x="834" y="100" width="34" height="22" fill="none" stroke="#2b2b2b" stroke-width="3"/><circle cx="851" cy="132" r="6" fill="#1c3766"/><rect x="838" y="138" width="26" height="4"/>
      <path d="M996 104h30a6 6 0 0 1 6 6v14a6 6 0 0 1-6 6h-18l-8 8v-8h-4a6 6 0 0 1-6-6v-14a6 6 0 0 1 6-6z" fill="none" stroke="#1c3766" stroke-width="3"/><circle cx="1004" cy="117" r="2.5"/><circle cx="1011" cy="117" r="2.5"/><circle cx="1018" cy="117" r="2.5"/>
    </g>
  </svg>

  <div class="why-item below" style="left:204px;top:432px"><h4>Market Research</h4><p>Duis autem vel eum iriure dolor in<br>hendrerit in vulputate.</p></div>
  <div class="why-item below" style="left:538px;top:432px"><h4>High Value</h4><p>Duis autem vel eum iriure dolor in<br>hendrerit in vulputate.</p></div>
  <div class="why-item below" style="left:871px;top:432px"><h4>Translate</h4><p>Duis autem vel eum iriure dolor in<br>hendrerit in vulputate.</p></div>
  <span class="dot-arrow" style="left:337px;top:514px;background:#1c3766"><svg width="8" height="10" viewBox="0 0 8 10"><path d="M1 1l5 4-5 4" stroke="#fff" stroke-width="2" fill="none"/></svg></span>
  <span class="dot-arrow" style="left:671px;top:514px;background:#1c3766"><svg width="8" height="10" viewBox="0 0 8 10"><path d="M1 1l5 4-5 4" stroke="#fff" stroke-width="2" fill="none"/></svg></span>
  <span class="dot-arrow" style="left:1004px;top:514px;background:#1c3766"><svg width="8" height="10" viewBox="0 0 8 10"><path d="M1 1l5 4-5 4" stroke="#fff" stroke-width="2" fill="none"/></svg></span>
</section>

<h2 class="sec-title" style="top:2436px">LATEST BLOG</h2>
<svg class="divider" style="top:2491px" viewBox="0 0 540 20"><line x1="0" y1="10" x2="255" y2="10" stroke="#ccc"/><line x1="285" y1="10" x2="540" y2="10" stroke="#ccc"/><path d="M264 4l12 12M276 4l-12 12" stroke="#aaa" stroke-width="2"/></svg>

<article class="blog-card" style="left:80px">
  <div class="blog-media" role="img" aria-label="Illustration of a hand touching a glowing circuit network" style="background:linear-gradient(135deg,#0d2a55,#3f8fd0)"></div>
  <div class="blog-date"><b>24</b><small>APR</small></div>
  <div class="blog-body"><h5>Lorem ipsum dolor sit amet,</h5><div class="meta">by admin &nbsp;|&nbsp; in news, business</div><p>Ut wisi enim ad minim veniam, quisvero exerci tation ullamcorper.</p></div>
</article>
<article class="blog-card" style="left:437px">
  <div class="blog-media" role="img" aria-label="Photo of business people joining puzzle pieces overhead" style="background:linear-gradient(135deg,#c7d1dc,#6f8196)"></div>
  <div class="blog-date"><b>24</b><small>APR</small></div>
  <div class="blog-body"><h5>Duis autem vel eum iriure dolo,</h5><div class="meta">by admin &nbsp;|&nbsp; in news, business</div><p>Ut wisi enim ad minim veniam, quisvero exerci tation ullamcorper.</p></div>
</article>
<article class="blog-card" style="left:791px">
  <div class="blog-media" role="img" aria-label="Photo of a desk with papers, calculator and coffee" style="background:linear-gradient(135deg,#d8c8ad,#7b6a55)"></div>
  <div class="blog-date"><b>24</b><small>APR</small></div>
  <div class="blog-body"><h5>Vel illum dolore eu feugiat nulla</h5><div class="meta">by admin &nbsp;|&nbsp; in news, business</div><p>Ut wisi enim ad minim veniam, quisvero exerci tation ullamcorper.</p></div>
</article>
<div class="pager"><span class="on"></span><span></span></div>

<footer class="site-footer" role="img" aria-label="Night city skyline backdrop">
  <div class="contact-col bordered" style="left:140px">
    <svg width="22" height="26" viewBox="0 0 22 26"><path d="M11 25S2 15 2 9a9 9 0 0 1 18 0c0 6-9 16-9 16z" fill="none" stroke="#9aa" stroke-width="2"/><circle cx="11" cy="9" r="3" fill="none" stroke="#9aa" stroke-width="2"/></svg>
    12 Lorem ipsum dolor 456 Sed diam, nonummy
  </div>
  <div class="contact-col bordered" style="left:440px">
    <svg width="24" height="24" viewBox="0 0 24 24"><path fill="none" stroke="#9aa" stroke-width="1.8" d="M6.6 10.8c1.4 2.8 3.8 5.1 6.6 6.6l2.2-2.2c.3-.3.7-.4 1-.2 1.1.4 2.3.6 3.6.6.6 0 1 .4 1 1V20c0 .6-.4 1-1 1C10.6 21 3 13.4 3 4c0-.6.4-1 1-1h3.5c.6 0 1 .4 1 1 0 1.3.2 2.5.6 3.6.1.3 0 .7-.2 1z"/></svg>
    Phone: (00) 123-456-7890
  </div>
  <div class="contact-col" style="left:732px">
    <svg width="24" height="24" viewBox="0 0 24 24"><path d="M2 11L22 2l-7 20-4-8z M11 14l11-12" fill="none" stroke="#9aa" stroke-width="1.8"/></svg>
    Email: info@kova.com
  </div>
  <div class="footer-brand">KOVA</div>
  <p class="footer-text">Lorem ipsum dolor sit amet, consectetuer adipiscing elit, sed diam nonummy nibh euismod tincidunt ut laoreet dolore magna aliquam</p>
  <div class="hours"><span>MON - FRI: 8:00 - 17:00</span><span>SATURDAY: 9:00 - 15:00</span><span>SUNDAY: CLOSED</span></div>
  <div class="footer-btn">CONTACT US</div>
  <div class="footer-rule"></div>
  <div class="copyright">Copyright © 2016 KOVA . All Right Reserved.</div>
  <span class="social" style="left:924px;background:#3b5998"></span>
  <span class="social" style="left:976px;background:#0e76a8"></span>
  <span class="social" style="left:1029px;background:#2aa3ef"></span>
  <span class="social" style="left:1082px;background:#d34836"></span>
</footer>

</body>
</html>
```